RW Holloway LLC Business Card - Civil Engineering & Consulting Firm

We need a Business Card that is elegant, and masculine.  It is our Professional Civil Engineering & Consulting Company located in San Antonio TX (Not s construction or builder firm- no gears & no tool images please). We provide civil engineering services including  commercial site plans, grading and drainage plans, utility plans, hydraulics and hydrology, land planning, utility coordination, and other general civil engineering services related to commercial and residential development.
We have 2 existing Logos. We would like to convey reliability, strength, trustworthiness and attention to detail.  Blues and orange tones as per logo We are OK with the use of a darker blue in the mix.  We have 2 logo versions - Full Company Name Logo to go on the back of card, & Small Icon Logo for the front w/ personal Info.

Target Market(s)
Architects, Real Estate Developers, Other Strctural Engineers, Surveyers, General Contractors
Industry/Entity Type
Professional Civil Engineering
Contact Information for Business Card
Name, Position, Address, Cell & Office #, email, and company website
Font styles to use
Other font styles liked:
- Avian
Requirements
Should not have
- No Tools, No Gears, no Cranes, or Construction Equipment.

```html
<!DOCTYPE html>
<html lang="en">
<head>
<meta charset="utf-8">
<title>RW Holloway LLC — Business Card</title>
<link rel="stylesheet" href="https://fonts.googleapis.com/css2?family=Montserrat:wght@600&family=Questrial&display=swap">
<style>
  :root {
    --backdrop: #6f6f6f;
    --navy: #002545;
    --sky: #6fa7d8;
    --orange: #f0922c;
    --white: #ffffff;
  }
  html, body {
    margin: 0;
    padding: 0;
    width: 1200px;
    height: 1200px;
    overflow: hidden;
    background: var(--backdrop);
  }
  .canvas {
    position: relative;
    width: 1200px;
    height: 1200px;
  }
  .card {
    position: absolute;
    left: 262px;
    width: 686px;
    height: 392px;
    overflow: hidden;
  }
  .card-front { top: 165px; background: var(--white); }
  .card-back { top: 653px; background: var(--navy); }

  .brand-name {
    position: absolute;
    left: 0;
    right: 0;
    text-align: center;
    font-family: "Questrial", sans-serif;
    color: var(--sky);
    letter-spacing: 0.08em;
    white-space: nowrap;
  }
  .brand-name .brand-square {
    display: inline-block;
    width: 0.42em;
    height: 0.42em;
    background: var(--orange);
    margin-right: 0.4em;
    vertical-align: 0.12em;
  }
  .card-front .brand-name { top: 96px; font-size: 46px; }
  .card-back .brand-name { top: 168px; font-size: 50px; }

  .info-band {
    position: absolute;
    left: 0;
    top: 242px;
    width: 686px;
    height: 150px;
    background: var(--navy);
  }
  .band-notch {
    position: absolute;
    left: 98px;
    top: 242px;
  }
  .person {
    position: absolute;
    left: 40px;
    top: 34px;
    font-family: "Questrial", sans-serif;
    color: var(--white);
  }
  .person-name {
    font-family: "Montserrat", sans-serif;
    font-weight: 600;
    font-size: 22px;
    line-height: 26px;
    color: var(--sky);
    letter-spacing: -0.01em;
  }
  .person-title {
    font-size: 16px;
    line-height: 18px;
    color: var(--orange);
  }
  .person-address {
    margin-top: 10px;
    font-size: 16px;
    line-height: 19px;
  }
  .contact-list {
    position: absolute;
    right: 40px;
    top: 50px;
    margin: 0;
    padding: 0;
    list-style: none;
    font-family: "Questrial", sans-serif;
    font-size: 16px;
    line-height: 19.5px;
    color: var(--white);
    text-align: right;
  }
  .contact-list li {
    display: flex;
    justify-content: flex-end;
    align-items: center;
    gap: 10px;
  }
  .contact-list svg {
    width: 12px;
    height: 12px;
    flex: none;
    fill: var(--orange);
  }
</style>
</head>
<body>
<div class="canvas">

  <section class="card card-front" aria-label="Business card front">
    <div class="brand-name"><span class="brand-square"></span>RW Holloway LLC</div>

    <div class="info-band">
      <div class="person">
        <div class="person-name">DANIEL REYES</div>
        <div class="person-title">President</div>
        <div class="person-address">2215 Mesquite Bend<br>San Antonio, Texas 78230</div>
      </div>

      <ul class="contact-list">
        <li>210-555-0147
          <svg viewBox="0 0 12 12" aria-hidden="true"><path d="M2.4 0.6 L4.3 2.6 L3.3 4 C3.9 5.5 5.6 7.3 7.1 8 L8.5 7 L10.6 8.9 L9.4 11 C5 10.6 1.2 6.6 0.9 2.1 Z"/></svg>
        </li>
        <li>210-555-0148
          <svg viewBox="0 0 12 12" aria-hidden="true"><path d="M3 0 H9 V12 H3 Z M4.2 1.4 V9.6 H7.8 V1.4 Z"/></svg>
        </li>
        <li>reyes@rwholloway.com
          <svg viewBox="0 0 12 12" aria-hidden="true"><path d="M0.5 2.5 H11.5 V3.2 L6 6.6 L0.5 3.2 Z M0.5 4.4 L6 7.8 L11.5 4.4 V9.5 H0.5 Z"/></svg>
        </li>
        <li>www.rwholloway.com
          <svg viewBox="0 0 12 12" aria-hidden="true"><circle cx="6" cy="6" r="5.6"/><path d="M3 3.5 L5.5 3 L6 5 L4.5 6.5 L3.5 5.5 Z M7 7 L9 6.5 L8.5 9 L7.2 9.2 Z" fill="#002545"/></svg>
        </li>
      </ul>
    </div>

    <svg class="band-notch" width="35" height="22" viewBox="0 0 35 22" aria-hidden="true">
      <polygon points="0,0 35,0 0,22" fill="#ffffff"/>
    </svg>
  </section>

  <section class="card card-back" aria-label="Business card back">
    <div class="brand-name"><span class="brand-square"></span>RW Holloway LLC</div>
  </section>

</div>
</body>
</html>
```